Bench Advertisement - We Buy Houses Design Needed

Need a catchy, simple but elegant design for bus benches to advertise our company.

We need our website, or phone number, and a smal description (1-2 bulletpoints of what we do and what we offer)

The tricky part is for the designer to fit everything and make the website name as part of the title and fitting everything so that people passing by on the street can see what we offer.

Our website is quickdealhomebuyer.com - (916) 555-0143

Something simple but something that catches the eye of walking pedestrians, and drivers driving by the bench.

Our company buys houses, any condition, any situation, we buy houses for cash and close quickly. You can use this description to create a few bulletpoints however you like. Must follow dimensions in attachment.

Target Market(s)

People in foreclosure, about to lose their homes, people that need a quick cash sale of their property

Industry/Entity Type

Real Estate

Requirements
Must have
• catchy, website name, phone number, few brief bulletpoints about what we offer, colors that will catch peoples eye while walking or driving - advertisement will be placed on bus benches - visit our website to see the type of houses we buy - Also have more work for winner of design with possible bonuses
Nice to have
• Feel free to use description or images on our website - make sure the description is just bullet points and it fits with the overall theme / size of the advertisement - Bold bright colors - put yourself in their shoes (if you were going through financial difficulties and about to lose your house to foreclosure or auction, what would you want to see to pick up the phone and call us for a quick sale of your house?) (or if you have a house that you are having a problem with, problem renters, unkept/beat up house, what would make you want to call us and sell your house to us?)

```html
<!DOCTYPE html>
<html lang="en">
<head>
<meta charset="utf-8">
<title>Quick Deal Home Buyer – Bench Advertisement</title>
<link href="https://fonts.googleapis.com/css2?family=Open+Sans:wght@400;600;700&family=PT+Sans+Narrow&display=swap" rel="stylesheet">
<style>
  :root {
    --teal: #3b8a98;
    --teal-light: #5fa8b5;
    --teal-dark: #2f7785;
    --text-grey: #6b6b6b;
    --caption-grey: #7a7a7a;
    --panel: #ffffff;
    --stage: #2b2b2b;
  }
  * { margin: 0; padding: 0; box-sizing: border-box; }
  html, body {
    width: 1200px; height: 768px; overflow: hidden;
    background: var(--stage);
  }
  .bench-ad {
    position: absolute;
    left: 20px; top: 223px;
    width: 1160px; height: 322px;
    background: var(--panel);
    font-family: "Open Sans", sans-serif;
  }
  .phone {
    position: absolute; left: 45px; top: 22px;
    font-weight: 700; font-size: 60px; line-height: 1;
    color: var(--teal); letter-spacing: 0.5px;
  }
  .website {
    position: absolute; left: 46px; top: 96px;
    font-weight: 600; font-size: 31px; line-height: 1;
    color: var(--teal); letter-spacing: 0.2px;
  }
  .offer-list {
    position: absolute; left: 50px; top: 146px;
    list-style: none;
    font-family: "PT Sans Narrow", sans-serif;
    font-size: 28px; line-height: 37px;
    color: var(--text-grey);
  }
  .offer-list li { display: flex; align-items: center; gap: 12px; }
  .offer-list svg { width: 18px; height: 18px; flex: none; }
  .steps {
    position: absolute; left: 40px; top: 230px;
    display: flex; gap: 12px;
  }
  .step { width: 100px; text-align: center; }
  .step-icon {
    width: 43px; height: 43px; margin: 0 auto 5px;
    border-radius: 50%;
    background: radial-gradient(circle at 40% 35%, var(--teal-light), var(--teal-dark));
    display: flex; align-items: center; justify-content: center;
  }
  .step-icon svg { width: 20px; height: 20px; }
  .step-label {
    font-size: 7px; line-height: 8px; color: var(--caption-grey);
    text-transform: uppercase;
  }
  .brand {
    position: absolute; left: 600px; top: 120px; width: 540px;
    display: flex; align-items: center; justify-content: center; gap: 16px;
  }
  .brand-mark { width: 34px; height: 34px; background: var(--teal); flex: none; }
  .brand-name {
    font-size: 36px; font-weight: 400; color: var(--teal);
    text-transform: uppercase; white-space: nowrap;
  }
</style>
</head>
<body>
  <section class="bench-ad">
    <div class="phone">Cell (916) 555-0143</div>
    <div class="website">QUICKDEALHOMEBUYER.COM</div>

    <ul class="offer-list">
      <li>
        <svg viewBox="0 0 18 18"><g fill="var(--teal)"><rect x="0" y="0" width="8" height="8"/><rect x="10" y="0" width="8" height="8"/><rect x="0" y="10" width="8" height="8"/><rect x="10" y="10" width="8" height="8"/></g></svg>
        Our company buys houses, any condition, any situation
      </li>
      <li>
        <svg viewBox="0 0 18 18"><g fill="var(--teal)"><rect x="0" y="0" width="8" height="8"/><rect x="10" y="0" width="8" height="8"/><rect x="0" y="10" width="8" height="8"/><rect x="10" y="10" width="8" height="8"/></g></svg>
        We buy houses for cash &amp; close quickly
      </li>
    </ul>

    <div class="steps">
      <div class="step">
        <div class="step-icon">
          <svg viewBox="0 0 20 20" fill="none" stroke="#fff" stroke-width="1.6"><rect x="4" y="3" width="12" height="14" rx="1"/><path d="M7 7h6M7 10h6M7 13h4"/></svg>
        </div>
        <div class="step-label">Fill out the form</div>
      </div>
      <div class="step">
        <div class="step-icon">
          <svg viewBox="0 0 20 20"><path fill="#fff" d="M5 3l3 0 1.5 4-2 1.3a9 9 0 0 0 4.2 4.2L13 10.5l4 1.5v3a2 2 0 0 1-2 2A13 13 0 0 1 3 5a2 2 0 0 1 2-2z"/></svg>
        </div>
        <div class="step-label">We'll call you within a few hours</div>
      </div>
      <div class="step">
        <div class="step-icon">
          <svg viewBox="0 0 20 20" fill="none" stroke="#fff" stroke-width="1.5" stroke-linejoin="round"><rect x="3" y="9" width="3" height="8"/><path d="M6 9l3-5c1.5 0 2 1 1.6 2.5L10 9h5a1.5 1.5 0 0 1 1.4 1.9l-1.5 5A1.5 1.5 0 0 1 13.5 17H6"/></svg>
        </div>
        <div class="step-label">We work with you on a solution</div>
      </div>
      <div class="step">
        <div class="step-icon">
          <svg viewBox="0 0 20 20"><path fill="#fff" d="M10 3l8 7h-2.5v7h-4v-4h-3v4h-4v-7H2z"/></svg>
        </div>
        <div class="step-label">Move on with your life</div>
      </div>
    </div>

    <div class="brand">
      <span class="brand-mark"></span>
      <span class="brand-name">Quick Deal Home Buyer</span>
    </div>
  </section>
</body>
</html>
```